Mastering Modern Vineyard Management

size of the ad - 8”x 10.75" plus 0.25" bleed
I would like an ad for a magazine that will stand out and make people want to read the ad.
The ad should not be crowded and people reading the ad will be able to read the text.
I would like it to be a creative and modern-day design.
the list of topics should not be the focus of the ad.
the text is attached.
If you decide to use people in the ad then please no ladies.
please note that leave over 1 inch for the bottom of the footer

```html
<!DOCTYPE html>
<html lang="en">
<head>
<meta charset="utf-8">
<title>Viticulture Course – Mastering Modern Vineyard Management</title>
<link rel="stylesheet" href="https://fonts.googleapis.com/css2?family=Bebas+Neue&family=Poppins:wght@400;500;600;700;800&display=swap">
<style>
  :root {
    --page: #ffffff;
    --navy: #050d1a;
    --navy-mid: #0b2340;
    --glow: #1f6fae;
    --yellow: #e8f01c;
    --cyan: #13b6d8;
    --white: #ffffff;
    --red: #e3131e;
    --ink: #1a1a1a;
    --muted: #d8dde6;
  }
  * { box-sizing: border-box; margin: 0; padding: 0; }
  html, body {
    width: 1200px; height: 2785px; overflow: hidden;
    background: var(--page);
    font-family: "Poppins", Arial, sans-serif;
  }
  .ad {
    position: absolute; left: 50px; top: 661px;
    width: 1100px; height: 1463px;
    background: var(--page);
    box-shadow: 0 10px 40px rgba(0,0,0,0.35);
    overflow: hidden;
  }
  .ad__panel {
    position: absolute; left: 0; top: 0;
    width: 1100px; height: 1331px;
    background: var(--navy);
  }
  .ad__title {
    position: absolute; left: 0; right: 0; top: 62px;
    text-align: center;
    font-family: "Bebas Neue", Impact, sans-serif;
    font-size: 150px; line-height: 1; color: var(--white);
    letter-spacing: -1px; font-weight: 400;
  }
  .ad__subtitle {
    position: absolute; left: 0; right: 0; top: 194px;
    text-align: center;
    font-weight: 700; font-size: 40px; line-height: 1;
    color: var(--yellow); letter-spacing: -0.5px;
  }
  .ad__visual {
    position: absolute; left: 0; top: 260px;
    width: 1100px; height: 522px;
    background:
      radial-gradient(ellipse 320px 230px at 550px 250px, rgba(60,160,230,0.55), transparent 70%),
      linear-gradient(180deg, var(--navy) 0%, var(--navy-mid) 35%, #124a7c 55%, var(--navy-mid) 80%, var(--navy) 100%);
  }
  .ad__slogan {
    position: absolute; left: 76px; top: 678px;
    font-weight: 800; font-size: 62px; line-height: 1.02;
    color: var(--white); letter-spacing: -0.5px;
  }
  .ad__slogan-accent { color: var(--yellow); display: block; }
  .session { position: absolute; left: 76px; top: 832px; width: 470px; }
  .session__town {
    font-weight: 800; font-size: 82px; line-height: 1;
    color: var(--cyan); letter-spacing: -1px;
  }
  .session__meta {
    margin-top: 14px;
    font-weight: 600; font-size: 40px; line-height: 1.06;
    color: var(--white);
  }
  .session__start {
    position: absolute; left: 0; top: 190px;
    width: 462px; height: 76px;
    border: 4px solid var(--cyan); border-radius: 14px;
    background: var(--navy);
    display: flex; overflow: hidden;
  }
  .session__start-label {
    background: var(--white); color: var(--ink);
    width: 178px; display: flex; align-items: center; justify-content: center;
    font-weight: 800; font-size: 28px;
  }
  .session__start-date {
    flex: 1; display: flex; align-items: center; justify-content: center;
    font-family: "Bebas Neue", Impact, sans-serif;
    font-size: 60px; color: var(--white); line-height: 1; padding-top: 4px;
  }
  .session__start-date .num { color: var(--yellow); }
  .session__start-date sup { font-size: 28px; color: var(--yellow); vertical-align: top; line-height: 1.2; margin-right: 10px; }
  .session__note {
    position: absolute; left: 2px; top: 284px;
    font-weight: 700; font-size: 27px; color: var(--white); white-space: nowrap;
  }
  .offer {
    position: absolute; left: 76px; top: 1160px;
    width: 466px; height: 142px;
    border: 4px solid var(--red); border-radius: 18px;
    background: var(--white); overflow: hidden;
  }
  .offer__head {
    background: var(--red); color: var(--white);
    height: 58px; padding-left: 18px;
    font-weight: 800; font-size: 42px; line-height: 60px; white-space: nowrap;
  }
  .offer__text {
    padding: 6px 18px 0; color: var(--ink);
    font-weight: 500; font-size: 27px; line-height: 1.2;
  }
  .topics { position: absolute; left: 604px; top: 842px; }
  .topics__heading {
    font-weight: 700; font-size: 34px; line-height: 1;
    color: var(--cyan); letter-spacing: -0.3px; white-space: nowrap;
  }
  .topics__list { list-style: none; margin-top: 20px; }
  .topics__item {
    display: flex; align-items: center; gap: 12px;
    height: 43.2px;
    font-size: 22px; color: var(--muted); white-space: nowrap;
  }
  .topics__tick { width: 16px; height: 16px; flex: none; }
</style>
</head>
<body>
  <main class="ad">
    <section class="ad__panel">
      <h1 class="ad__title">VITICULTURE COURSE</h1>
      <p class="ad__subtitle">MASTERING MODERN VINEYARD MANAGEMENT</p>

      <div class="ad__visual" role="img" aria-label="Photo of a businessman touching a glowing digital icon inside a shield, surrounded by hexagonal tech icons on a deep blue background"></div>

      <h2 class="ad__slogan">
        <span class="ad__slogan-accent">INVESTING IN KNOWLEDGE IS</span>
        INVESTING IN OPPORTUNITIES.
      </h2>

      <div class="session">
        <p class="session__town">ASHVALE</p>
        <p class="session__meta">10 -TUESDAY<br>EVENINGS SESSIONS</p>
        <div class="session__start">
          <span class="session__start-label">STARTING</span>
          <span class="session__start-date"><span class="num">28</span><sup>TH</sup>FEBRUARY</span>
        </div>
        <p class="session__note">LIMITED PARTIAL SCHOLARSHIPS</p>
      </div>

      <div class="offer">
        <p class="offer__head">EARLY BIRD SPECIAL</p>
        <p class="offer__text">For those that started or would like to go into viticulture</p>
      </div>

      <section class="topics">
        <h3 class="topics__heading">TOPICS: PARTIAL LISTING</h3>
        <ul class="topics__list">
          <li class="topics__item"><svg class="topics__tick" viewBox="0 0 16 16"><circle cx="8" cy="8" r="6.5" fill="none" stroke="#d8dde6" stroke-width="1.4"/><path d="M5 8.2l2 2 4-4" fill="none" stroke="#d8dde6" stroke-width="1.4"/></svg>Vineyard investment strategies</li>
          <li class="topics__item"><svg class="topics__tick" viewBox="0 0 16 16"><circle cx="8" cy="8" r="6.5" fill="none" stroke="#d8dde6" stroke-width="1.4"/><path d="M5 8.2l2 2 4-4" fill="none" stroke="#d8dde6" stroke-width="1.4"/></svg>Site selection</li>
          <li class="topics__item"><svg class="topics__tick" viewBox="0 0 16 16"><circle cx="8" cy="8" r="6.5" fill="none" stroke="#d8dde6" stroke-width="1.4"/><path d="M5 8.2l2 2 4-4" fill="none" stroke="#d8dde6" stroke-width="1.4"/></svg>Financing</li>
          <li class="topics__item"><svg class="topics__tick" viewBox="0 0 16 16"><circle cx="8" cy="8" r="6.5" fill="none" stroke="#d8dde6" stroke-width="1.4"/><path d="M5 8.2l2 2 4-4" fill="none" stroke="#d8dde6" stroke-width="1.4"/></svg>Soil and irrigation</li>
          <li class="topics__item"><svg class="topics__tick" viewBox="0 0 16 16"><circle cx="8" cy="8" r="6.5" fill="none" stroke="#d8dde6" stroke-width="1.4"/><path d="M5 8.2l2 2 4-4" fill="none" stroke="#d8dde6" stroke-width="1.4"/></svg>Canopy management</li>
          <li class="topics__item"><svg class="topics__tick" viewBox="0 0 16 16"><circle cx="8" cy="8" r="6.5" fill="none" stroke="#d8dde6" stroke-width="1.4"/><path d="M5 8.2l2 2 4-4" fill="none" stroke="#d8dde6" stroke-width="1.4"/></svg>Vineyard legal basics</li>
          <li class="topics__item"><svg class="topics__tick" viewBox="0 0 16 16"><circle cx="8" cy="8" r="6.5" fill="none" stroke="#d8dde6" stroke-width="1.4"/><path d="M5 8.2l2 2 4-4" fill="none" stroke="#d8dde6" stroke-width="1.4"/></svg>Pest control</li>
          <li class="topics__item"><svg class="topics__tick" viewBox="0 0 16 16"><circle cx="8" cy="8" r="6.5" fill="none" stroke="#d8dde6" stroke-width="1.4"/><path d="M5 8.2l2 2 4-4" fill="none" stroke="#d8dde6" stroke-width="1.4"/></svg>Harvest timing</li>
          <li class="topics__item"><svg class="topics__tick" viewBox="0 0 16 16"><circle cx="8" cy="8" r="6.5" fill="none" stroke="#d8dde6" stroke-width="1.4"/><path d="M5 8.2l2 2 4-4" fill="none" stroke="#d8dde6" stroke-width="1.4"/></svg>Dealing with wineries</li>
          <li class="topics__item"><svg class="topics__tick" viewBox="0 0 16 16"><circle cx="8" cy="8" r="6.5" fill="none" stroke="#d8dde6" stroke-width="1.4"/><path d="M5 8.2l2 2 4-4" fill="none" stroke="#d8dde6" stroke-width="1.4"/></svg>Tax fundamentals</li>
        </ul>
      </section>
    </section>
  </main>
</body>
</html>
```